Business Card Design for Marketing Firm

Looking for business card design for higher end marketing firm. Clean but impressionable/trendy. We are a marketing firm that represents manufacturers in the foodservice equipment and supply industry. Our customers are end users such has hotels, restaurants, country clubs, convention centers and casinos as well as distributors of restaurants supplies and equipment, and manufacturers of foodservice equipment and supplies.
Target Market(s)
Hotels, Restaurants, Supply & Equipment Distributors, Foodservice Manufacturers
Industry/Entity Type
Foodservice/Hospitality
Contact Information for Business Card
Name, Title, Contact Number, Email, Website, Social Media, Address
Requirements
Must have
- Clean & Simple but Serious and Impressionable

```html
<!DOCTYPE html>
<html lang="en">
<head>
<meta charset="utf-8">
<title>Harbor Service Partners – Business Cards</title>
<link rel="stylesheet" href="https://fonts.googleapis.com/css2?family=Open+Sans:wght@400;600;700&display=swap">
<style>
  :root {
    --navy: #262673;
    --ink: #2b2b2b;
    --paper: #ffffff;
    --stage: #e9e9ec;
  }
  * { margin: 0; padding: 0; box-sizing: border-box; }
  html, body {
    width: 1200px; height: 786px; overflow: hidden;
    background: var(--stage);
    font-family: "Open Sans", Arial, sans-serif;
  }
  .canvas {
    position: relative; width: 1200px; height: 786px;
    display: flex; align-items: center; justify-content: center; gap: 50px;
  }
  .card {
    position: relative; width: 540px; height: 309px;
    background: var(--paper);
    box-shadow: 0 6px 22px rgba(0,0,0,.14);
    overflow: hidden;
  }
  /* contact side */
  .card-wave { position: absolute; inset: 0; width: 100%; height: 100%; }
  .brand {
    position: absolute; left: 34px; top: 100px; width: 220px;
    display: flex; align-items: center; gap: 10px;
  }
  .brand-dot {
    width: 26px; height: 26px; flex: none; border-radius: 50%;
    background: var(--navy);
  }
  .brand-name {
    color: var(--navy); font-weight: 600; font-size: 17px;
    line-height: 1.25; letter-spacing: .06em; text-transform: uppercase;
  }
  .divider {
    position: absolute; left: 272px; top: 40px; width: 1.5px; height: 150px;
    background: var(--navy);
  }
  .contact { position: absolute; left: 292px; top: 38px; color: var(--ink); }
  .contact-name {
    color: var(--navy); font-weight: 700; font-size: 18px; line-height: 1.1;
  }
  .contact-title { font-size: 11.5px; margin-bottom: 10px; }
  .contact-list { list-style: none; font-size: 12px; line-height: 1.55; }
  .contact-list li { display: flex; align-items: center; gap: 7px; }
  .contact-list svg { width: 11px; height: 11px; fill: var(--navy); flex: none; }
  .contact-address { font-size: 12px; line-height: 1.4; margin-top: 10px; padding-left: 18px; }

  /* brand side */
  .card-back {
    display: flex; flex-direction: column; align-items: center; justify-content: center; gap: 16px;
    border-bottom: 8px solid var(--navy);
  }
  .card-back .brand-dot { width: 44px; height: 44px; }
  .card-back .brand-name { font-size: 26px; text-align: center; }
  .social { display: flex; gap: 5px; }
  .social span { width: 13px; height: 13px; border-radius: 50%; background: var(--navy); }
</style>
</head>
<body>
<main class="canvas">
  <section class="card card-front" aria-label="Contact side">
    <svg class="card-wave" viewBox="0 0 540 309" preserveAspectRatio="none" aria-hidden="true">
      <path fill="#262673" d="M0,309 L0,292 C110,236 240,232 350,208 C430,190 495,160 540,128 L540,309 Z"/>
      <path fill="none" stroke="#262673" stroke-width="3" d="M0,276 C110,220 240,212 350,192 C430,178 495,148 540,114"/>
    </svg>
    <div class="brand">
      <span class="brand-dot"></span>
      <span class="brand-name">Harbor Service Partners</span>
    </div>
    <div class="divider"></div>
    <div class="contact">
      <p class="contact-name">DANIEL REED</p>
      <p class="contact-title">Managing Director</p>
      <ul class="contact-list">
        <li><svg viewBox="0 0 24 24"><path d="M6.6 10.8a15.1 15.1 0 0 0 6.6 6.6l2.2-2.2a1 1 0 0 1 1-.25 11.4 11.4 0 0 0 3.6.57 1 1 0 0 1 1 1V20a1 1 0 0 1-1 1A17 17 0 0 1 3 4a1 1 0 0 1 1-1h3.5a1 1 0 0 1 1 1c0 1.25.2 2.45.57 3.57a1 1 0 0 1-.25 1z"/></svg>123 456 789</li>
        <li><svg viewBox="0 0 24 24"><path d="M2 5h20v14H2z M4 7v.5l8 5 8-5V7l-8 5z" fill-rule="evenodd"/></svg>info@yourmail.com</li>
        <li><svg viewBox="0 0 24 24"><circle cx="12" cy="12" r="10"/></svg>www.yourwebsite.com</li>
      </ul>
      <p class="contact-address">Your address, City<br>State, Zip 1234</p>
    </div>
  </section>

  <section class="card card-back" aria-label="Brand side">
    <span class="brand-dot"></span>
    <span class="brand-name">Harbor Service<br>Partners</span>
    <div class="social" aria-label="Social media links">
      <span></span><span></span><span></span><span></span><span></span><span></span>
    </div>
  </section>
</main>
</body>
</html>
```